Boutique Health and Fitness Personal Training Studio

I would like to have a brochure designed which provides a detailed description of the services offered in my business.
I have personal training studio, We look after people from early 20's to 90's, healthy to very unhealthy.
We conduct:
A consultation
An assessment
A personalised program
Personalised training sessions
I would like to base the design around the colours of my logo (attached) and use some of (or all of) the images and information I have also attached.
I would be happy with your own images included also.

Target Market(s)

20 to 90 year olds

Industry/Entity Type

Business

Font styles to use
Serif
Sans Serif

Colors
9bcb3c
add136
cadf82
eaf2ce

Requirements
Must have
• Colour and images of fitness.
• 8.5x14 legal
• Tri fold
• 2 folds with 3 faces back n front
Nice to have
• The feeling of wellbeing
Should not have
• This is not a gym.
• It should have the feel of a private relaxed environment

```html
<!DOCTYPE html>
<html lang="en">
<head>
<meta charset="utf-8">
<title>Evergreen Wellness Studio – Tri-fold Brochure</title>
<link href="https://fonts.googleapis.com/css2?family=Lato:wght@400;700;900&family=Roboto+Condensed:wght@400;700&display=swap" rel="stylesheet">
<style>
:root{
  --green:#6a9a2c;
  --green-deep:#4d7619;
  --green-light:#9bcb3c;
  --charcoal:#2a2b2a;
  --paper:#f3f3f1;
  --grey:#d9dad8;
  --text-dark:#2b2b2b;
  --white:#ffffff;
  --backdrop:#e7e5e1;
}
*{margin:0;padding:0;box-sizing:border-box}
html,body{width:907px;height:1200px;overflow:hidden}
body{background:var(--backdrop);font-family:"Lato",sans-serif;position:relative}
.spread{position:absolute;left:52px;width:801px;height:486px;overflow:hidden;box-shadow:0 4px 14px rgba(0,0,0,.35)}
.spread--outside{top:84px}
.spread--inside{top:615px}
.spread svg.shapes{position:absolute;inset:0}
.panel{position:absolute;top:0;height:486px;width:267px}
.heading{font-family:"Roboto Condensed",sans-serif;font-weight:700;font-size:14px;line-height:1.2}
.body{font-size:8.6px;line-height:1.38;text-align:justify}
.on-green{color:var(--white)}
.on-green .heading{color:var(--white)}
.brand{display:flex;align-items:center;gap:6px;font-family:"Lato",sans-serif;font-weight:700;font-size:15px;white-space:nowrap}
.brand__dot{width:14px;height:14px;border-radius:50%;background:var(--green)}
.brand--light{color:var(--white)}
.brand--light .brand__dot{background:var(--white)}
.brand--green{color:var(--green)}

/* outside */
.sessions{left:0;padding:36px 18px 0 30px}
.sessions .body{text-align:left}
.sessions .heading{font-size:13px;margin-bottom:4px}
.sessions .gap{margin-top:14px}
.sessions .big{font-size:12px;margin-top:4px}
.parking{position:absolute;left:30px;top:230px;width:214px;height:24px;background:var(--green-deep);border-radius:3px;font-family:"Roboto Condensed",sans-serif;font-weight:700;font-size:14px;color:#dfeec0;display:flex;align-items:center;justify-content:center;box-shadow:0 3px 6px rgba(0,0,0,.35)}
.contact{left:266px;text-align:center;padding-top:84px}
.contact .brand{justify-content:center;font-size:16px;margin-bottom:20px}
.contact .unit{font-family:"Roboto Condensed",sans-serif;font-weight:700;font-size:14px;line-height:1.25;color:#111}
.contact .addr{font-size:9.5px;font-weight:700;margin-top:6px;color:#111}
.contact .call{font-family:"Roboto Condensed",sans-serif;font-weight:700;font-size:13px;margin-top:3px;color:#111}
.contact .call span{font-size:10px}
.contact .visit{font-family:"Roboto Condensed",sans-serif;font-weight:700;font-size:13px;margin-top:6px;color:#111}
.contact .web{font-size:9px;font-weight:700;color:#111}
.cover{left:534px}
.cover__claim{position:absolute;right:26px;top:346px;text-align:right;font-family:"Roboto Condensed",sans-serif;text-transform:uppercase;color:var(--white)}
.cover__claim strong{display:block;font-size:24px;color:var(--green-light);font-weight:700;line-height:1}
.cover__claim span{display:block;font-size:13px;line-height:1.35}
.cover .brand{position:absolute;right:32px;top:428px;font-size:17px}

/* inside */
.care{left:0}
.care__text{position:absolute;left:30px;top:268px;width:222px}
.care .heading{color:var(--green-deep);font-size:13.5px}
.care .body{color:var(--text-dark);margin-top:3px}
.care .second{margin-top:9px}
.care .brand{position:absolute;left:56px;top:424px}
.care__bar{position:absolute;left:0;bottom:0;width:267px;height:14px;background:var(--charcoal)}
.process{left:266px;padding:34px 20px 0 28px}
.process .heading{margin-bottom:3px}
.process .body{font-size:8.4px;line-height:1.33}
.process .body+.heading{margin-top:8px}
.program{left:534px;padding:30px 20px 0 22px}
.program .heading{margin-bottom:6px}
.program .body+.heading{margin-top:24px}
</style>
</head>
<body>

<section class="spread spread--outside">
  <svg class="shapes" width="801" height="486" viewBox="0 0 801 486">
    <defs>
      <linearGradient id="paperFade" x1="0" x2="1">
        <stop offset="0" stop-color="#e4e5e3"/><stop offset=".5" stop-color="#f7f7f6"/><stop offset="1" stop-color="#d8d9d7"/>
      </linearGradient>
      <linearGradient id="stillLife" x1="0" y1="0" x2="0" y2="1">
        <stop offset="0" stop-color="#eeeeec"/><stop offset=".45" stop-color="#b9c79a"/><stop offset="1" stop-color="#8a6b4c"/>
      </linearGradient>
      <linearGradient id="gymTop" x1="0" y1="0" x2="1" y2="1">
        <stop offset="0" stop-color="#5d6a5a"/><stop offset=".6" stop-color="#3a3b36"/><stop offset="1" stop-color="#1e1f1d"/>
      </linearGradient>
      <linearGradient id="stretch" x1="0" y1="0" x2="1" y2="1">
        <stop offset="0" stop-color="#b54545"/><stop offset=".5" stop-color="#cfc8c2"/><stop offset="1" stop-color="#8d8f90"/>
      </linearGradient>
    </defs>
    <rect x="0" y="0" width="267" height="486" fill="var(--green)"/>
    <path d="M0 270 Q160 255 267 380 L267 486 L0 486 Z" fill="var(--white)"/>
    <path d="M0 282 Q150 270 258 392 L258 486 L0 486 Z" role="img" aria-label="Photo of a trainer assisting a client with a shoulder stretch" fill="url(#stretch)"/>
    <rect x="266" y="0" width="268" height="486" fill="url(#paperFade)"/>
    <rect x="266" y="296" width="268" height="190" role="img" aria-label="Photo of fresh vegetables, a dumbbell, a tape measure and a water bottle" fill="url(#stillLife)"/>
    <rect x="533" y="0" width="268" height="486" fill="var(--white)"/>
    <path d="M533 258 Q640 252 801 250 L801 486 L533 486 Z" fill="var(--green)"/>
    <path d="M533 292 Q640 262 801 262 L801 486 L533 486 Z" fill="var(--charcoal)"/>
    <path d="M560 0 L801 0 L801 240 Q700 260 620 225 Q560 190 560 120 Z" fill="var(--green)"/>
    <path d="M568 0 L801 0 L801 230 Q700 250 625 216 Q568 182 568 110 Z" role="img" aria-label="Photo of a man training on a cable machine" fill="url(#gymTop)"/>
  </svg>

  <div class="panel sessions on-green">
    <h2 class="heading">Your sessions</h2>
    <p class="body">Training at the studio is professional and caring, but focused and challenging. Typically each session will take approximately 60 minutes. Training times can be organized to suit your needs with early mornings and evenings available.</p>
    <h2 class="heading gap">The Cost</h2>
    <p class="big">$45 paid in blocks of 5 or 10 sessions</p>
    <h2 class="heading gap" style="margin-top:10px">Health fund claimable</h2>
    <p class="big">Open 7 days</p>
  </div>
  <div class="parking">Ample private parking available</div>

  <div class="panel contact">
    <div class="brand brand--green"><span class="brand__dot"></span>Evergreen Wellness Studio</div>
    <p class="unit">Unit 12<br>Level 2</p>
    <p class="addr">48 Wattle Grove Lane Hillcrest</p>
    <p class="call">call-<span>0400 555 019</span></p>
    <p class="visit">visit us</p>
    <p class="web">www.evergreenwellness.example</p>
  </div>

  <div class="panel cover">
    <p class="cover__claim"><strong>Over 25 years</strong><span>of experience managing</span><span>personal health and fitness</span></p>
    <div class="brand brand--light"><span class="brand__dot"></span>Evergreen Wellness Studio</div>
  </div>
</section>

<section class="spread spread--inside">
  <svg class="shapes" width="801" height="486" viewBox="0 0 801 486">
    <defs>
      <linearGradient id="paperFade2" x1="0" x2="1">
        <stop offset="0" stop-color="#f6f6f5"/><stop offset="1" stop-color="#dcdddb"/>
      </linearGradient>
      <linearGradient id="treadmill" x1="0" y1="0" x2="1" y2="1">
        <stop offset="0" stop-color="#6f7377"/><stop offset=".55" stop-color="#c9cfd2"/><stop offset="1" stop-color="#e9ecec"/>
      </linearGradient>
      <linearGradient id="yoga" x1="0" y1="0" x2="0" y2="1">
        <stop offset="0" stop-color="#d9a68c"/><stop offset=".5" stop-color="#e78fb4"/><stop offset="1" stop-color="#2b2b2b"/>
      </linearGradient>
      <linearGradient id="lunge" x1="0" y1="0" x2="1" y2="0">
        <stop offset="0" stop-color="#1c1c1c"/><stop offset=".7" stop-color="#2d3440"/><stop offset="1" stop-color="#1d4e8a"/>
      </linearGradient>
    </defs>
    <rect x="0" y="0" width="267" height="486" fill="url(#paperFade2)"/>
    <path d="M0 0 L225 0 Q280 80 245 160 Q205 240 80 240 Q30 238 0 225 Z" fill="var(--green)"/>
    <path d="M0 0 L215 0 Q262 80 232 155 Q198 228 80 228 Q30 226 0 214 Z" role="img" aria-label="Photo of a woman walking on a treadmill" fill="url(#treadmill)"/>
    <rect x="266" y="0" width="268" height="486" fill="var(--green)"/>
    <rect x="320" y="338" width="144" height="144" rx="56" role="img" aria-label="Photo of a smiling woman seated cross-legged holding a dumbbell and a plate of vegetables" fill="url(#yoga)"/>
    <rect x="533" y="0" width="268" height="486" fill="var(--green)"/>
    <path d="M533 486 L533 360 Q600 262 801 258 L801 486 Z" fill="#4e7420"/>
    <path d="M548 486 L548 372 Q615 278 801 272 L801 486 Z" fill="var(--white)"/>
    <rect x="560" y="290" width="236" height="190" rx="40" role="img" aria-label="Silhouette photo of a trainer guiding a woman through a lunge" fill="url(#lunge)" opacity=".9"/>
  </svg>

  <div class="panel care">
    <div class="care__text">
      <h2 class="heading">Personalised Care in<br>Fitness and Health</h2>
      <p class="body">Exercise programs for all levels of health and fitness and all age groups. Experience in managing a wide range of chronic health conditions.</p>
      <h2 class="heading second">Experienced professionals<br>caring for your wellbeing</h2>
      <p class="body">Exercise Physiologist with over 25 years of experience managing the health and fitness needs of the community.</p>
    </div>
    <div class="brand brand--green"><span class="brand__dot"></span>Evergreen Wellness Studio</div>
    <div class="care__bar"></div>
  </div>

  <div class="panel process on-green">
    <h2 class="heading">What to Expect</h2>
    <p class="body">On arrival at the studio you will be asked to complete a questionnaire, which will provide us with information regarding your background with health and fitness, as well as your goals and objectives. Please bring any relevant medical information from medical practitioners or health professionals that you feel may impact on your program.</p>
    <h2 class="heading">Consultation</h2>
    <p class="body">A consultation will allow you to share your thoughts, concerns and objectives, as well as provide you with ample opportunity to expand on the answers from your questionnaire relating to your prior and current health, medical and physical concerns.</p>
    <h2 class="heading">Assessment</h2>
    <p class="body">An assessment will be conducted to provide us both with a baseline measure of your cardiovascular fitness, strength, flexibility, balance and body composition measures. These measures provide us with a reference for program design and also to indicate improvements along the way.</p>
  </div>

  <div class="panel program on-green">
    <h2 class="heading">The program</h2>
    <p class="body">Your program will be designed with consideration to your health and fitness background, you objectives and your strengths and weaknesses. It will be personally tailored to your needs and provide you with a plan to focus your energies on.</p>
    <h2 class="heading">Nutrition</h2>
    <p class="body">Nutrition is central to an effective program, as it will provide you with maximal energy for exercise as well as keeping yourself lean and healthy for a long term fitter lifestyle. Evergreen Wellness Studio provides initial monitoring and ongoing modification in accordance with your needs.</p>
  </div>
</section>

</body>
</html>
```